design a construction company business card

Design business card around our logo. Card must have all the typical info: name, title, address, phone, email, business name, etc. Somewhere on the card I would like to see our motto "Built on trust... Driven by craftsmanship." Consider adding a splash of bright orange to the card to complement the blues and silvers/grays in the logo. We are open to metallic inks, textures, etc. We would like to see options on both light and dark backgrounds. The font in the logo is Euro Technic Extended Regular.

```html
<!DOCTYPE html>
<html lang="en">
<head>
<meta charset="UTF-8">
<title>Halden Contracting – Business Card</title>
<link href="https://fonts.googleapis.com/css2?family=Michroma&family=Lato:wght@400&family=Roboto+Condensed:wght@400&display=swap" rel="stylesheet">
<style>
  :root {
    --backdrop: #8b8b8b;
    --paper: #ffffff;
    --brand-blue: #1f4fb0;
    --brand-blue-light: #1a6cc4;
    --brand-blue-deep: #1e3386;
    --ink-grey: #555a60;
    --rule-grey: #9a9a9a;
    --white: #ffffff;
  }
  * { margin: 0; padding: 0; box-sizing: border-box; }
  html, body { width: 1200px; height: 1200px; overflow: hidden; }
  body { background: var(--backdrop); position: relative; }

  .card {
    position: absolute;
    top: 310px;
    height: 594px;
    box-shadow: 2px 3px 6px rgba(0,0,0,0.35);
  }
  .card-front { left: 234px; width: 364px; background: var(--paper); text-align: center; }
  .card-back {
    left: 627px; width: 370px;
    background: linear-gradient(180deg, var(--brand-blue-light) 0%, var(--brand-blue) 55%, var(--brand-blue-deep) 100%);
    text-align: center;
  }

  .company-name {
    font-family: "Michroma", sans-serif;
    font-weight: 400;
    color: var(--brand-blue);
  }
  .company-name .name-main { display: block; font-size: 44px; letter-spacing: 2px; line-height: 1; }
  .company-name .name-sub { display: block; font-size: 15px; letter-spacing: 0.5px; margin-top: 12px; }

  .card-front .company-name { position: absolute; top: 188px; left: 0; right: 0; }
  .card-back .company-name { position: absolute; top: 258px; left: 0; right: 0; color: var(--white); }

  .person-name {
    position: absolute; top: 334px; left: 0; right: 0;
    font-family: "Michroma", sans-serif; font-size: 20px; color: var(--brand-blue);
    letter-spacing: 0.5px;
  }
  .person-title {
    position: absolute; top: 360px; left: 0; right: 0;
    font-family: "Lato", sans-serif; font-size: 16px; color: var(--ink-grey);
  }
  .contact-icons { position: absolute; top: 394px; left: 87px; }
  .contact-lines {
    position: absolute; top: 430px; left: 0; right: 0;
    font-family: "Lato", sans-serif; font-size: 16.5px; line-height: 22px; color: var(--ink-grey);
  }
  .contact-divider {
    position: absolute; top: 506px; left: 88px; width: 194px; height: 1px; background: #dcdcdc;
  }
  .address-lines {
    position: absolute; top: 517px; left: 0; right: 0;
    font-family: "Lato", sans-serif; font-size: 16.5px; line-height: 22px; color: var(--ink-grey);
  }

  .motto {
    position: absolute; top: 355px; left: 0; right: 0;
    font-family: "Roboto Condensed", sans-serif; font-size: 15px; color: var(--white);
    text-transform: uppercase; letter-spacing: 0.1px;
  }
</style>
</head>
<body>

<section class="card card-front">
  <div class="company-name">
    <span class="name-main">HALDEN</span>
    <span class="name-sub">CONTRACTING, INC.</span>
  </div>

  <div class="person-name">MARCUS ELLERY</div>
  <div class="person-title">Managing Director</div>

  <svg class="contact-icons" width="190" height="28" viewBox="0 0 190 28" aria-hidden="true">
    <line x1="0" y1="14" x2="54" y2="14" stroke="var(--rule-grey)" stroke-width="1"/>
    <line x1="136" y1="14" x2="190" y2="14" stroke="var(--rule-grey)" stroke-width="1"/>
    <circle cx="67" cy="14" r="12" fill="var(--brand-blue)"/>
    <circle cx="95" cy="14" r="12" fill="var(--brand-blue)"/>
    <circle cx="123" cy="14" r="12" fill="var(--brand-blue)"/>
    <path d="M60 12 q7 -6 14 0 l-2 2 h-2 l-1 -2 h-4 l-1 2 h-2 z M62 15 h10 v4 h-10 z" fill="var(--white)"/>
    <rect x="88" y="9" width="14" height="10" fill="none" stroke="var(--white)" stroke-width="1.5"/>
    <polyline points="88,9 95,15 102,9" fill="none" stroke="var(--white)" stroke-width="1.5"/>
    <circle cx="123" cy="14" r="7" fill="none" stroke="var(--white)" stroke-width="1.5"/>
    <ellipse cx="123" cy="14" rx="3" ry="7" fill="none" stroke="var(--white)" stroke-width="1.2"/>
    <line x1="116" y1="14" x2="130" y2="14" stroke="var(--white)" stroke-width="1.2"/>
  </svg>

  <div class="contact-lines">
    044-987 654 321<br>
    info@haldenbuild.com<br>
    www.haldenbuild.com
  </div>
  <div class="contact-divider"></div>
  <div class="address-lines">
    421, Address line here,<br>
    45452,Country Name
  </div>
</section>

<section class="card card-back">
  <div class="company-name">
    <span class="name-main">HALDEN</span>
    <span class="name-sub">CONTRACTING, INC.</span>
  </div>
  <div class="motto">Built on trust... Driven by craftsmanship</div>
</section>

</body>
</html>
```